Smack you in the face - Landing page for Residential Electrical Repairs (Searchly Ads)

I need an effective landing page for Searchly ads. The ads will target residential electrical repairs. Lighting Outages, Power Outages, Breakers Tripping, Outlets Not Working. I need a strong call to action to Call Us Now! Forms don't work well for us so we only need one form as a last option at the bottom of the page. We only work on homes. the website is https://www.vantor-wiring.example/
email is : support@vantor-wiring.example
Phone 555-217-4086

**This is about one focused service. Electrical Repairs - That includes Partial Power Outages, Outlets Not Working, Tripped Breakers, Electrical Panel repairs, and Fusebox Repairs. The area served will only be Greenville, SC. KOBA is the platform

Target Market(s)

Homeonwers in need of electrical repair

Industry/Entity Type

Residential Electricians

Coding

Coded - Design and coding required

Requirements
Must have
• Strong to action for phone calls, this landing page must grab action fast.
Nice to have
• Social proof with existing 5 start reviews for Searchly, Rately, TCB, and Friendnet
Should not have
• Should not be form based. I do not like the site's current them, please don't copy it. Make your own.

```html
<!DOCTYPE html>
<html lang="en">
<head>
<meta charset="utf-8">
<title>Vantor Wiring Service – Residential Electrical Repairs</title>
<link rel="stylesheet" href="https://fonts.googleapis.com/css2?family=Archivo+Black&family=Montserrat:ital,wght@0,400;0,500;0,600;0,700;1,400;1,500&display=swap">
<style>
:root{
  --blue:#2a93c6;
  --blue-dark:#1f7fb0;
  --orange:#f26b21;
  --ink:#1c1c1c;
  --dark:#1f1f21;
  --grey-bg:#efefef;
  --pale-blue:#e9f3f7;
  --text:#3a3a3a;
  --white:#fff;
}
*{box-sizing:border-box;margin:0;padding:0}
html,body{width:1200px;height:4619px;overflow:hidden}
body{position:relative;font-family:"Montserrat",sans-serif;color:var(--text);background:var(--white)}
.abs{position:absolute}
.heading{font-family:"Archivo Black",sans-serif;color:var(--ink);text-transform:uppercase;line-height:1.1}
.tag{background:var(--blue);color:var(--white);padding:0 10px;display:inline-block}
.eyebrow{font-size:16px;letter-spacing:2px;text-transform:uppercase}
.btn{display:flex;align-items:center;justify-content:center;gap:8px;border-radius:40px;font-weight:700;text-transform:uppercase;text-decoration:none;white-space:nowrap}
.btn svg{width:18px;height:18px}
.photo{position:absolute}

/* header */
.site-header{position:absolute;left:0;top:0;width:1200px;height:77px;background:var(--white);box-shadow:0 2px 6px rgba(0,0,0,.08);z-index:5}
.brand{display:flex;align-items:center;gap:8px;font-family:"Archivo Black",sans-serif;font-size:16px;color:var(--ink);letter-spacing:.5px;white-space:nowrap;width:175px}
.brand-dot{width:18px;height:18px;border-radius:50%;background:var(--blue);flex:none}
.nav{position:absolute;top:30px;display:flex;font-size:13px;font-weight:600;color:var(--ink)}
.nav a{position:absolute;white-space:nowrap;color:inherit;text-decoration:none}
.nav a.active{border-bottom:3px solid var(--orange);padding-bottom:6px}

/* hero */
.hero{position:absolute;left:0;top:77px;width:1200px;height:635px;background:linear-gradient(90deg,#232325 0%,#2c2d30 60%,#3a3c40 100%);overflow:hidden}
.hero-title{font-size:40px;color:var(--white);line-height:56px}

/* cards */
.service-card{position:absolute;top:664px;width:309px;height:170px;text-align:center;border-radius:4px}
.service-card .icon{position:absolute;left:50%;top:-30px;width:64px;height:64px;margin-left:-32px;border-radius:50%;background:var(--white);border:3px solid #ddd;display:flex;align-items:center;justify-content:center}
.service-card h3{margin-top:54px;font-size:15px;font-weight:700;text-transform:uppercase}
.service-card p{font-size:11px;line-height:16px;margin:8px auto 0;width:250px}
.service-card .btn{width:114px;height:28px;margin:10px auto 0;font-size:9px}

/* tiles */
.tile{position:absolute;width:455px;height:246px;overflow:hidden}
.tile .photo{inset:0}
.tile .label{position:absolute;left:0;bottom:0;width:100%;height:35px;background:rgba(30,30,30,.65);color:var(--white);font-weight:600;font-size:17px;text-align:center;line-height:35px}

/* reviews */
.review{position:absolute;top:3082px;width:316px;height:242px;background:var(--white);border:2px solid #d8dde0;border-radius:4px;padding:42px 36px 0}
.review p{font-style:italic;font-size:12.5px;line-height:19px;color:#333}
.review .name{margin-top:14px;font-weight:700;font-size:13px;color:var(--ink)}
.review .stars{color:var(--orange);font-size:15px;letter-spacing:1px}
.review .platform{position:absolute;right:18px;bottom:18px;display:flex;align-items:center;gap:6px;font-size:13px;font-weight:700;color:var(--blue)}
.review .platform span.sq{width:12px;height:12px;border-radius:50%;background:var(--blue)}

/* form */
.field{position:absolute;background:var(--white);font-size:11px;color:#444;padding:12px 16px}
</style>
</head>
<body>

<header class="site-header">
  <div class="brand abs" style="left:102px;top:28px"><span class="brand-dot"></span>VANTOR WIRING</div>
  <nav class="nav" style="left:0">
    <a class="active" style="left:327px">HOME</a>
    <a style="left:430px">ABOUT US</a>
    <a style="left:563px">SERVICES</a>
    <a style="left:692px">REVIEWS</a>
    <a style="left:816px">CONTACT</a>
  </nav>
  <a class="btn abs" style="left:920px;top:18px;width:183px;height:40px;background:var(--blue);color:var(--white);font-size:14px" href="tel:5552174086">
    <svg viewBox="0 0 24 24"><circle cx="12" cy="12" r="12" fill="#fff"/><path d="M8.5 6.5l2 2-1.2 1.5c.7 1.6 2 2.9 3.7 3.7l1.5-1.2 2 2-1.3 1.8C11 16 8 13 6.8 7.8z" fill="#2a93c6"/></svg>555-217-4086</a>
</header>

<section class="hero">
  <div class="photo" role="img" aria-label="Smiling electrician in cap and work shirt at an outdoor electrical panel" style="left:390px;top:0;width:810px;height:635px;background:linear-gradient(120deg,#5c6b7a 0%,#8a7a66 45%,#6b8a4c 100%);clip-path:polygon(350px 0,810px 0,810px 635px,60px 635px)"></div>
  <svg class="abs" style="left:0;top:0" width="1200" height="635" viewBox="0 0 1200 635">
    <polygon points="740,0 380,635 430,635 500,470 470,400" fill="var(--blue)"/>
  </svg>
  <div class="abs eyebrow" style="left:122px;top:162px;color:#e6e6e6;font-size:17px">VANTOR WIRING SERVICES</div>
  <div class="abs heading hero-title" style="left:124px;top:184px">YOUR TRUSTED SOURCE<br>FOR <span class="tag">ELECTRICAL</span><br>SOLUTION</div>
  <a class="btn abs" style="left:126px;top:366px;width:200px;height:46px;background:var(--orange);color:var(--white);font-size:12px">CONTACT US NOW</a>
</section>

<div class="service-card" style="left:117px;background:#efefef;color:var(--ink)">
  <div class="icon"><svg width="30" height="30" viewBox="0 0 24 24"><path d="M3 11l9-7 9 7v9H3z" fill="none" stroke="#333" stroke-width="1.6"/><path d="M12 10l-2 4h3l-2 4" fill="none" stroke="#333" stroke-width="1.6"/></svg></div>
  <h3>Electrical Repairs</h3>
  <p>Lorem ipsum dolor sit amet consectetur adipiscing elit sed do eiusmod</p>
  <a class="btn" style="background:var(--blue);color:#fff">CONTACT US</a>
</div>
<div class="service-card" style="left:434px;background:var(--blue);color:var(--white)">
  <div class="icon"><svg width="30" height="30" viewBox="0 0 24 24"><rect x="4" y="5" width="16" height="15" fill="none" stroke="#333" stroke-width="1.6"/><path d="M8 9v8M12 9v8M16 9v8" stroke="#333" stroke-width="1.6"/></svg></div>
  <h3>Emergency Service</h3>
  <p>Lorem ipsum dolor sit amet consectetur adipiscing elit sed do eiusmod</p>
  <a class="btn" style="background:#fff;color:var(--blue)">CONTACT US</a>
</div>
<div class="service-card" style="left:759px;background:var(--orange);color:var(--white)">
  <div class="icon"><svg width="30" height="30" viewBox="0 0 24 24"><circle cx="12" cy="8" r="4" fill="none" stroke="#333" stroke-width="1.6"/><path d="M4 21c1-5 4-7 8-7s7 2 8 7" fill="none" stroke="#333" stroke-width="1.6"/></svg></div>
  <h3 style="margin-top:46px">24/7 On Call</h3>
  <p>Lorem ipsum dolor sit amet consectetur adipiscing elit sed do eiusmod</p>
  <a class="btn" style="background:#fff;color:var(--orange)">CONTACT US</a>
</div>

<section class="about">
  <div class="photo" role="img" aria-label="Smiling electrician in cap and glasses opening a home electrical panel" style="left:152px;top:880px;width:390px;height:591px;background:linear-gradient(160deg,#e4e7ea 0%,#b8c4cf 55%,#7b8c9c 100%);clip-path:polygon(0 100%,0 20%,100% 0,100% 100%)"></div>
  <svg class="abs" style="left:152px;top:876px" width="390" height="595" viewBox="0 0 390 595"><polygon points="390,20 230,300 280,330 0,560 170,420 120,390" fill="var(--blue)" opacity=".85"/></svg>
  <div class="abs eyebrow" style="left:618px;top:955px;color:var(--blue);font-size:15px">WHO WE ARE</div>
  <h2 class="abs heading" style="left:617px;top:982px;font-size:37px;line-height:46px">ABOUT VANTOR<br>ELECTRICAL <span class="tag">SERVICE</span></h2>
  <p class="abs" style="left:621px;top:1097px;width:495px;font-size:14px;line-height:23.5px">At Vantor Wiring, EV Chargers, &amp; Generators, your electrical emergency is our urgency. We have Licensed Electricians in Greenville, SC, Raleigh, NC, and Charlotte, NC, ensuring top-tier service for every call. We've built our reputation as the go-to Emergency Electrician for homeowners in need.</p>
  <p class="abs" style="left:621px;top:1238px;width:495px;font-size:14px;line-height:23.5px">When you find yourself thinking about an "electrician near me," think of us. While many electricial contractors chase after large-scale construction and commercial building projects, we prioritize you – the homeowner. We're committed to delivering unbeatable same-day service for all your residential electrical repairs, EV chargers, and Generator installations.</p>
</section>

<section class="abs" style="left:0;top:1471px;width:1200px;height:768px;background:var(--grey-bg)">
  <svg class="abs" style="left:0;top:0" width="1200" height="768"><polygon points="1075,55 1040,260 870,260" fill="#d4d4d4"/><polygon points="1060,230 1165,290 1060,395" fill="#d4d4d4"/></svg>
  <div class="abs eyebrow" style="left:0;width:1200px;text-align:center;top:70px;color:#333;font-size:16px">WHAT WE DO</div>
  <h2 class="abs heading" style="left:0;width:1200px;text-align:center;top:98px;font-size:33px">ELECTRICAL <span class="tag">REPAIRS</span></h2>
</section>
<div class="tile" style="left:135px;top:1656px"><div class="photo" role="img" aria-label="Hands stripping wires with pliers" style="background:linear-gradient(135deg,#3b3b3b,#8c7d6e 60%,#4a4a4a)"></div><div class="label">LIGHTING OUTAGES</div></div>
<div class="tile" style="left:605px;top:1656px"><div class="photo" role="img" aria-label="Electrician working inside a breaker panel" style="background:linear-gradient(135deg,#5a6470,#9a8f7f 55%,#c2b59c)"></div><div class="label" style="background:var(--blue)">POWER OUTAGES</div></div>
<div class="tile" style="left:135px;top:1920px"><div class="photo" role="img" aria-label="Hand holding a circuit breaker" style="background:linear-gradient(135deg,#2a2a2a,#6e6e6e 50%,#b08a6c)"></div><div class="label">BREAKERS TRIPPING</div></div>
<div class="tile" style="left:605px;top:1920px"><div class="photo" role="img" aria-label="Electrician installing a wall mounted charger" style="background:linear-gradient(135deg,#d8d8d8,#8a96a4 55%,#3f4a56)"></div><div class="label">OUTLETS NOT WORKING</div></div>

<section class="abs" style="left:0;top:2239px;width:1200px;height:115px;background:var(--orange)">
  <svg class="abs" style="left:115px;top:18px" width="80" height="80" viewBox="0 0 80 80"><polygon points="70,2 20,42 40,44 2,78 60,34 40,32" fill="#fff"/></svg>
  <div class="abs" style="left:205px;top:40px;font-size:26px;color:#fff;font-weight:700;white-space:nowrap">NEED ELECTRICAL SERVICE NOW!</div>
  <a class="btn abs" style="left:807px;top:34px;width:232px;height:54px;background:#fff;color:var(--ink);font-size:18px" href="tel:5552174086"><svg viewBox="0 0 24 24"><path d="M6 3l4 4-2 3c1.3 2.7 3.3 4.7 6 6l3-2 4 4-3 3C10 20 4 14 3 6z" fill="#1c1c1c"/></svg>CALL US NOW</a>
</section>

<section class="abs" style="left:0;top:2354px;width:1200px;height:549px;background:var(--blue);overflow:hidden">
  <div class="photo" role="img" aria-label="Electrician testing an outlet with a digital multimeter" style="left:0;top:0;width:1200px;height:549px;background:linear-gradient(120deg,#9aa3aa 30%,#6c7278 60%,#c8a232 85%,#3a3a3a);clip-path:polygon(760px 0,1200px 0,1200px 549px,470px 549px,660px 330px,565px 310px,700px 180px)"></div>
  <div class="abs eyebrow" style="left:131px;top:82px;color:#fff;font-size:15px">WHY WE ARE</div>
  <h2 class="abs heading" style="left:130px;top:108px;font-size:30px;line-height:38px;color:#fff">WHY CHOOSE VANTOR<br>ELECTRICAL <span class="tag" style="background:#fff;color:var(--blue)">SERVICE</span></h2>
  <div class="abs" style="left:131px;top:216px;display:flex;flex-direction:column;gap:20px;color:#fff">
    <div style="display:flex;gap:14px;align-items:center"><span style="width:54px;height:54px;border-radius:50%;background:#fff;display:flex;align-items:center;justify-content:center"><svg width="26" height="26" viewBox="0 0 24 24"><rect x="3" y="5" width="18" height="16" fill="none" stroke="#2a93c6" stroke-width="1.8"/><path d="M3 10h18M8 3v4M16 3v4" stroke="#2a93c6" stroke-width="1.8"/></svg></span><div><div style="font-weight:700;font-size:16px">On-Time Appointments</div><div style="font-size:12px;margin-top:3px">Lorem ipsum dolor sit amet, consectetur</div></div></div>
    <div style="display:flex;gap:14px;align-items:center"><span style="width:54px;height:54px;border-radius:50%;background:#fff;display:flex;align-items:center;justify-content:center;color:var(--blue);font-weight:700;font-size:12px">24/7</span><div><div style="font-weight:700;font-size:16px">Same-Day Service</div><div style="font-size:12px;margin-top:3px">Lorem ipsum dolor sit amet, consectetur adipi</div></div></div>
    <div style="display:flex;gap:14px;align-items:center"><span style="width:54px;height:54px;border-radius:50%;background:#fff;display:flex;align-items:center;justify-content:center"><svg width="26" height="26" viewBox="0 0 24 24"><circle cx="12" cy="12" r="9" fill="none" stroke="#2a93c6" stroke-width="1.8"/><path d="M7.5 12l3 3 6-6" fill="none" stroke="#2a93c6" stroke-width="2"/></svg></span><div><div style="font-weight:700;font-size:16px">100% Satisfaction Guarantee</div><div style="font-size:12px;margin-top:3px">Lorem ipsum dolor sit amet, consect</div></div></div>
  </div>
</section>

<section class="abs" style="left:0;top:2903px;width:1200px;height:538px;background:var(--pale-blue)">
  <div class="abs eyebrow" style="left:0;width:1200px;text-align:center;top:70px;color:#333">TESTIMONIALS</div>
  <h2 class="abs heading" style="left:0;width:1200px;text-align:center;top:100px;font-size:33px">CUSTOMER <span class="tag">REVIEWS</span></h2>
  <svg class="abs" style="left:58px;top:270px" width="20" height="36"><path d="M17 2L3 18l14 16" fill="none" stroke="#8a9399" stroke-width="3"/></svg>
  <svg class="abs" style="left:1133px;top:270px" width="20" height="36"><path d="M3 2l14 16L3 34" fill="none" stroke="#8a9399" stroke-width="3"/></svg>
</section>
<div class="review" style="left:120px"><p>"Lorem ipsum dolor sit amet, consectetur adipiscing elit, sed do eiusmod tempor incididunt ut labore et dolore magna aliqua Quis ipsum suspendisse ultrices gravida Risus commodo viverra maecenas"</p><div class="name">Dana Whitfield</div><div class="stars">★★★★★</div><div class="platform"><span class="sq"></span>Searchly</div></div>
<div class="review" style="left:454px"><p>"Lorem ipsum dolor sit amet, consectetur adipiscing elit, sed do eiusmod tempor incididunt ut labore et dolore magna aliqua Quis ipsum suspendisse ultrices gravida Risus commodo viverra maecenas"</p><div class="name">Dana Whitfield</div><div class="stars">★★★★★</div><div class="platform"><span class="sq"></span>Rately</div></div>
<div class="review" style="left:784px"><p>"Lorem ipsum dolor sit amet, consectetur adipiscing elit, sed do eiusmod tempor incididunt ut labore et dolore magna aliqua Quis ipsum suspendisse ultrices gravida Risus commodo viverra maecenas"</p><div class="name">Dana Whitfield</div><div class="stars">★★★★★</div><div class="platform"><span class="sq"></span>Friendnet</div></div>

<section class="area">
  <div class="abs eyebrow" style="left:150px;top:3550px;color:var(--blue);font-size:15px">WHERE WE SERVE</div>
  <h2 class="abs heading" style="left:149px;top:3578px;font-size:37px">AREA WE <span class="tag">SERVE</span></h2>
  <p class="abs" style="left:150px;top:3642px;width:400px;font-size:14.5px;line-height:27px">Lorem ipsum dolor sit amet, consectetur adipiscing elit, sed do eiusmod tempor incididunt ut labore et dolore magna aliqua. Quis ipsum suspendisse ultrices gravida. Risus commodo viverra maecenas</p>
  <a class="btn abs" style="left:152px;top:3800px;width:232px;height:54px;background:var(--blue);color:#fff;font-size:18px" href="tel:5552174086"><svg viewBox="0 0 24 24"><path d="M6 3l4 4-2 3c1.3 2.7 3.3 4.7 6 6l3-2 4 4-3 3C10 20 4 14 3 6z" fill="#fff"/></svg>CALL US NOW</a>
  <div class="photo" role="img" aria-label="Outline map of South Carolina counties" style="left:565px;top:3495px;width:502px;height:407px;background:radial-gradient(ellipse at center,#e3eff6 0%,#f4f9fc 70%,#fff 100%)"></div>
</section>

<svg class="abs" style="left:0;top:4300px" width="1200" height="319"><polygon points="0,20 1200,-30 1200,319 0,319" fill="var(--dark)"/></svg>

<section class="abs" style="left:170px;top:3956px;width:844px;height:430px;background:var(--blue)">
  <div class="abs eyebrow" style="left:0;width:844px;text-align:center;top:56px;color:#fff;font-size:13px">CONTACT US NOW</div>
  <h2 class="abs" style="left:0;width:844px;text-align:center;top:76px;font-size:26px;color:#fff;font-weight:700">SEND US AN ENQUIRY</h2>
  <div class="field" style="left:95px;top:122px;width:318px;height:40px">Name</div>
  <div class="field" style="left:427px;top:122px;width:320px;height:40px">Email address</div>
  <div class="field" style="left:95px;top:175px;width:318px;height:40px">Phone</div>
  <div class="field" style="left:427px;top:175px;width:320px;height:40px">Type of Service</div>
  <div class="field" style="left:95px;top:230px;width:652px;height:93px">Message</div>
  <a class="btn abs" style="left:356px;top:346px;width:131px;height:36px;background:var(--orange);color:#fff;font-size:12px">SUBMIT</a>
</section>

<footer>
  <div class="brand abs" style="left:131px;top:4455px;color:#fff"><span class="brand-dot"></span>VANTOR WIRING</div>
  <nav class="nav" style="left:0;top:4456px;color:#fff;font-size:14px">
    <a style="left:334px">HOME</a><a style="left:450px">ABOUT US</a><a style="left:597px">SERVICES</a><a style="left:741px">CONTACT US</a>
  </nav>
  <a class="btn abs" style="left:908px;top:4444px;width:183px;height:40px;background:var(--orange);color:#fff;font-size:14px" href="tel:5552174086"><svg viewBox="0 0 24 24"><circle cx="12" cy="12" r="12" fill="#fff"/><path d="M8.5 6.5l2 2-1.2 1.5c.7 1.6 2 2.9 3.7 3.7l1.5-1.2 2 2-1.3 1.8C11 16 8 13 6.8 7.8z" fill="#f26b21"/></svg>555-217-4086</a>
  <div class="abs" style="left:0;top:4548px;width:1200px;height:1px;background:#444"></div>
  <div class="abs" style="left:142px;top:4571px;font-size:11px;color:#ddd">© 2023 <u>Vantor Wiring Service.</u> All Right Reserved</div>
  <div class="abs" style="left:836px;top:4565px;display:flex;align-items:center;gap:10px;font-size:13px;color:#fff"><svg width="26" height="26" viewBox="0 0 24 24"><circle cx="12" cy="12" r="12" fill="#fff"/><rect x="6" y="8" width="12" height="8" fill="none" stroke="#1f1f21" stroke-width="1.4"/><path d="M6 8l6 5 6-5" fill="none" stroke="#1f1f21" stroke-width="1.4"/></svg>support@vantor-wiring.example</div>
</footer>

</body>
</html>
```